U.S. Popcorn company needs business cards

We are a popcorn company that manufactures popcorn and sells it to grocery stores worldwide. Our theme is "Americana" and our logo is U.S. route 66 which is the most famous highway in the U.S.

We would like the design to be simple and to use both sides. On the back side we would like to see just the logo and website. The front would be normal details

Target Market(s)

Wholesalers, grocers and distributors

Industry/Entity Type

Manufacture

Contact Information for Business Card

Business name: Prairie Lantern Popcorn
Phone: +1 555 308 4726
Email: Dale@prairielanternpopcorn.com
website: www.prairielanternpopcorn.com
Tag Line: "POPular for a reason"
Name: Dale Whitcombe
Title: Founder/President

Requirements
Must have
• Either this design should be fun or clean and simple. I will let you show me your thougths.
Nice to have
• Anything that ties in the real Hwy Route 66.
• Colors might need to be red, white and blue incorporated.
Should not have
• Not be too busy.

```html
<!DOCTYPE html>
<html lang="en">
<head>
<meta charset="utf-8">
<title>Prairie Lantern Popcorn – Business Cards</title>
<link rel="stylesheet" href="https://fonts.googleapis.com/css2?family=Mulish:wght@400;800&display=swap">
<style>
  :root {
    --backdrop: #222222;
    --card: #141414;
    --card-edge: #2a2a2a;
    --red: #e0261f;
    --white: #f2f2f2;
    --silver: #9a9a9a;
    --blue: #1d3f8c;
  }
  * { box-sizing: border-box; margin: 0; padding: 0; }
  html, body {
    width: 1200px; height: 793px; overflow: hidden;
    background: var(--backdrop);
    font-family: "Mulish", "Century Gothic", sans-serif;
  }
  .canvas { position: relative; width: 1200px; height: 793px; }
  .card {
    position: absolute; top: 248px;
    width: 520px; height: 297px;
    background: var(--card);
    border: 1px solid var(--card-edge);
    border-radius: 10px;
  }
  .card--back { left: 50px; }
  .card--front { left: 630px; }

  /* Back */
  .back-mark {
    position: absolute; inset: 0;
    display: flex; align-items: center; justify-content: center; gap: 14px;
  }
  .back-mark__dot {
    width: 22px; height: 22px; border-radius: 50%;
    background: var(--silver);
  }
  .back-mark__name {
    color: var(--silver); font-weight: 800; font-size: 26px;
    line-height: 1.15; text-transform: uppercase; letter-spacing: 1px;
  }

  /* Front */
  .person { position: absolute; left: 34px; top: 72px; }
  .person__name { color: var(--red); font-weight: 800; font-size: 20px; }
  .person__title { color: var(--white); font-size: 14px; margin-top: 2px; }

  .brand {
    position: absolute; right: 40px; top: 46px;
    display: flex; align-items: center; gap: 12px;
  }
  .brand__dot { width: 20px; height: 20px; border-radius: 50%; background: var(--red); }
  .brand__name {
    color: var(--white); font-weight: 800; font-size: 24px;
    line-height: 1.15; text-transform: uppercase; letter-spacing: 1px;
  }

  .tagline {
    position: absolute; right: 48px; top: 182px;
    color: var(--white); font-size: 16px;
  }
  .tagline__pop { color: var(--red); font-weight: 800; }

  .contacts {
    position: absolute; left: 34px; bottom: 26px;
    list-style: none; color: var(--white); font-size: 13px;
  }
  .contacts li { display: flex; align-items: center; gap: 12px; line-height: 20px; }
  .contacts svg { width: 12px; height: 12px; fill: var(--red); flex: none; }
  .contacts .accent { color: var(--red); }
</style>
</head>
<body>
<main class="canvas">

  <section class="card card--back" aria-label="Card back">
    <div class="back-mark">
      <span class="back-mark__dot"></span>
      <span class="back-mark__name">Prairie Lantern<br>Popcorn</span>
    </div>
  </section>

  <section class="card card--front" aria-label="Card front">
    <div class="person">
      <p class="person__name">Dale Whitcombe</p>
      <p class="person__title">Founder/President</p>
    </div>

    <div class="brand">
      <span class="brand__dot"></span>
      <span class="brand__name">Prairie Lantern<br>Popcorn</span>
    </div>

    <p class="tagline">"<span class="tagline__pop">POP</span>ular for a reason"</p>

    <ul class="contacts">
      <li>
        <svg viewBox="0 0 12 12" aria-hidden="true"><path d="M1 3c0-1 1-2 2-2h6c1 0 2 1 2 2v1H8V3H4v1H1zM2 5h8l1 6H1z"/></svg>
        +1 555 308 4726
      </li>
      <li>
        <svg viewBox="0 0 12 12" aria-hidden="true"><path d="M0 2h12v8H0zM1 3v.5l5 3.5 5-3.5V3z" fill-rule="evenodd"/></svg>
        Dale@prairielanternpopcorn.com
      </li>
      <li>
        <svg viewBox="0 0 12 12" aria-hidden="true"><circle cx="6" cy="6" r="5.5"/><path d="M0.5 6h11M6 0.5v11" stroke="#141414" stroke-width="1"/></svg>
        <span>www.<span class="accent">prairielanternpopcorn</span>.com</span>
      </li>
    </ul>
  </section>

</main>
</body>
</html>
```